Computer consultant business card

Bexil Software is a newly started computer consulting company. It's a small one-man company that provides mostly Vornix applications but also websites in collaboration with designers. I'm running this company on the side of full time university studies.

I want the final design to be clean and memorable. Be creative! :)

Some inspiration:
http://www.pixelmarta.com/design/48317
http://www.pixelmarta.com/design/2739164/business-card-design-by-frostlynk
http://www.pixelmarta.com/design/604281/business-card-design-by-koralind-vestrabanu

See attachment for my company logo.
Updates

I would like to thank everyone for submitting! I'll need a couple of days to review and ultimately select a design.

Target Market(s)

Non-technical entrepreneurs and small companies.

Industry/Entity Type

University

Requirements
Must have
• My company logo.
In any way, both colors from my logo.
First- and last name, e-mail and phone number.
Double-sided design.
Nice to have
• Something creative with the symbol in my logo

```html
<!DOCTYPE html>
<html lang="en">
<head>
<meta charset="utf-8">
<title>Bexil Software — Business Card</title>
<link rel="stylesheet" href="https://fonts.googleapis.com/css2?family=Exo+2:wght@400;500;600&family=Crimson+Text&display=swap">
<style>
  :root {
    --page: #e9e8e6;
    --slate: #363b42;
    --slate-deep: #2c3036;
    --paper: #f4f4f4;
    --ink: #3a3b3e;
    --accent: #5b86c5;
    --contact: #e6e8ec;
  }
  * { box-sizing: border-box; margin: 0; padding: 0; }
  html, body { width: 1200px; height: 900px; overflow: hidden; }
  body {
    background: var(--page);
    font-family: "Exo 2", sans-serif;
    display: flex;
    flex-direction: column;
    align-items: center;
    justify-content: center;
    gap: 44px;
  }
  .card {
    position: relative;
    width: 630px;
    height: 360px;
    overflow: hidden;
    box-shadow: 0 6px 18px rgba(0,0,0,0.18);
  }
  .wordmark {
    display: flex;
    align-items: center;
    gap: 18px;
    color: var(--ink);
    font-weight: 500;
    letter-spacing: 1px;
  }
  .wordmark__dot {
    border-radius: 50%;
    background: var(--accent);
  }

  /* Front */
  .card--front { background: var(--slate); }
  .card--front .band {
    position: absolute;
    left: 0; right: 0;
    top: 82px;
    height: 156px;
    background: var(--paper);
    display: flex;
    align-items: center;
    justify-content: center;
  }
  .card--front .wordmark { font-size: 84px; }
  .card--front .wordmark__dot { width: 58px; height: 58px; }

  /* Back */
  .card--back { background: var(--slate); }
  .card--back .split { position: absolute; inset: 0; }
  .card--back .wordmark {
    position: absolute;
    left: 150px; top: 86px;
    font-size: 64px;
  }
  .card--back .wordmark__dot { width: 44px; height: 44px; }
  .holder {
    position: absolute;
    left: 40px; bottom: 34px;
    color: var(--accent);
    font-family: "Crimson Text", serif;
    font-size: 30px;
    line-height: 1.1;
  }
  .holder__role {
    display: block;
    font-family: "Exo 2", sans-serif;
    font-size: 14px;
    color: var(--contact);
    letter-spacing: 1px;
  }
  .contact {
    position: absolute;
    right: 34px; top: 168px;
    list-style: none;
    color: var(--contact);
    font-size: 15px;
    line-height: 27px;
  }
  .contact li { display: flex; align-items: center; gap: 10px; }
  .contact svg { width: 15px; height: 15px; fill: var(--accent); flex: none; }
  .contact .contact__address { padding-left: 0; }
</style>
</head>
<body>

  <section class="card card--front" aria-label="Card front">
    <div class="band">
      <div class="wordmark"><span class="wordmark__dot"></span>bexil</div>
    </div>
  </section>

  <section class="card card--back" aria-label="Card back">
    <svg class="split" viewBox="0 0 630 360" preserveAspectRatio="none" aria-hidden="true">
      <polygon points="0,0 630,0 630,70 0,300" fill="#f4f4f4"/>
      <line x1="0" y1="302" x2="630" y2="72" stroke="#5b86c5" stroke-width="2"/>
    </svg>
    <div class="wordmark"><span class="wordmark__dot"></span>bexil</div>
    <p class="holder">Tomas Rekvik<span class="holder__role">App Developer</span></p>
    <ul class="contact">
      <li><svg viewBox="0 0 16 16"><path d="M3.5 1.5l2.6 2.6-1.5 2a8 8 0 0 0 5.3 5.3l2-1.5 2.6 2.6-1.8 2C7 15.8.2 9 1.5 3.3z"/></svg>+1 555 014 2287</li>
      <li><svg viewBox="0 0 16 16"><path d="M1 3h14v10H1z M1.8 3.8L8 9l6.2-5.2" stroke="#363b42" stroke-width="1"/></svg>hello@bexilsoft.net</li>
      <li><svg viewBox="0 0 16 16"><circle cx="8" cy="8" r="7"/><path d="M1 8h14M8 1c3 3 3 11 0 14M8 1c-3 3-3 11 0 14" stroke="#363b42" stroke-width="1" fill="none"/></svg>www.bexilsoft.net</li>
      <li class="contact__address">4820 Orrin Ave Kestler, CA 9034</li>
    </ul>
  </section>

</body>
</html>
```